Modern business card design for professional copywriter

I'd like a business card design that I can use to have my cards printed out by quillprint.com as a squared corners business card (see artwork and design guidelines here: https://help.quillprint.com/hc/en-gb/sections/200570950-QUILL-Product-Templates)

The design should be clean and modern and reflect the colours, tone and branding on my website: https://tessavorrin.com.au

Target Market(s)

Professionals, B2B small business owners

Industry/Entity Type

Business

Contact Information for Business Card

Tessa Vorrin
m: 0468 905 327
e: tessa@tessavorrin.com.au
w: tessavorrin.com.au

Font styles to use
Sans Serif

Requirements
Must have
• Tagline: "Smart copywriting for clever business people"
• Brand colours: fd8000, 009984, 666666 and black
Nice to have

```html
<!DOCTYPE html>
<html lang="en">
<head>
<meta charset="utf-8">
<title>Tessa Vorrin – Business Card</title>
<link rel="stylesheet" href="https://fonts.googleapis.com/css2?family=Jost:wght@400;500&display=swap">
<style>
  :root {
    --orange: #fd8000;
    --teal: #009984;
    --grey: #666666;
    --card: #141414;
    --stage: #2b2b2b;
    --white: #f2f2f2;
  }
  * { margin: 0; padding: 0; box-sizing: border-box; }
  html, body { width: 1200px; height: 900px; overflow: hidden; }
  body {
    background: var(--stage);
    font-family: "Jost", "Futura", sans-serif;
    position: relative;
  }
  .card {
    position: absolute;
    left: 250px;
    width: 700px;
    height: 400px;
    background: var(--card);
  }
  .card--front { top: 45px; }
  .card--back { top: 465px; }

  .wordmark {
    font-weight: 500;
    letter-spacing: -0.5px;
    line-height: 1;
    white-space: nowrap;
  }
  .card--front .wordmark {
    position: absolute;
    top: 140px;
    left: 0; right: 0;
    text-align: center;
    font-size: 54px;
    color: var(--grey);
  }
  .tagline {
    position: absolute;
    top: 262px;
    left: 0; right: 0;
    text-align: center;
    font-size: 17px;
    letter-spacing: 1.2px;
    color: var(--orange);
  }

  .card--back .wordmark {
    position: absolute;
    top: 172px;
    left: 48px;
    font-size: 46px;
    color: var(--teal);
  }
  .divider {
    position: absolute;
    width: 3px;
    background: var(--teal);
  }
  .divider--name { left: 395px; top: 108px; height: 58px; }
  .divider--contact { left: 395px; top: 198px; height: 96px; }

  .identity {
    position: absolute;
    left: 418px;
    top: 106px;
  }
  .identity__name { font-size: 26px; color: var(--orange); line-height: 1.15; }
  .identity__role { font-size: 22px; color: var(--white); line-height: 1.15; }

  .contact {
    position: absolute;
    left: 418px;
    top: 204px;
    list-style: none;
  }
  .contact__item {
    display: flex;
    align-items: center;
    gap: 14px;
    font-size: 18px;
    letter-spacing: 1px;
    color: var(--white);
    height: 30px;
  }
  .contact__icon { width: 16px; height: 16px; flex: none; }
</style>
</head>
<body>

  <section class="card card--front" aria-label="Card front">
    <div class="wordmark">Tessa Vorrin</div>
    <p class="tagline">Smart copywriting for clever business people</p>
  </section>

  <section class="card card--back" aria-label="Card back">
    <div class="wordmark">Tessa Vorrin</div>

    <span class="divider divider--name"></span>
    <div class="identity">
      <div class="identity__name">Tessa Vorrin</div>
      <div class="identity__role">Copywriter</div>
    </div>

    <span class="divider divider--contact"></span>
    <ul class="contact">
      <li class="contact__item">
        <svg class="contact__icon" viewBox="0 0 16 16" aria-hidden="true">
          <rect x="4" y="1" width="8" height="14" rx="1.5" fill="none" stroke="#fd8000" stroke-width="1.6"/>
          <line x1="7" y1="12.5" x2="9" y2="12.5" stroke="#fd8000" stroke-width="1.4"/>
        </svg>
        0468 905 327
      </li>
      <li class="contact__item">
        <svg class="contact__icon" viewBox="0 0 16 16" aria-hidden="true">
          <rect x="1" y="3.5" width="14" height="9" fill="#fd8000"/>
          <polyline points="1,3.5 8,9 15,3.5" fill="none" stroke="#141414" stroke-width="1.4"/>
        </svg>
        tessa@tessavorrin.com.au
      </li>
      <li class="contact__item">
        <svg class="contact__icon" viewBox="0 0 16 16" aria-hidden="true">
          <circle cx="6.5" cy="6.5" r="4.5" fill="none" stroke="#fd8000" stroke-width="2"/>
          <line x1="10" y1="10" x2="14.5" y2="14.5" stroke="#fd8000" stroke-width="2.4" stroke-linecap="round"/>
        </svg>
        tessavorrin.com.au
      </li>
    </ul>
  </section>

</body>
</html>
```